Business Card for Vorla Parts Wholesale supplier

Hi There! I need a new business card for our company. We are specialized in selling Vorla parts, mostly we sell new LCD screens for Zelnar and Drelks. I would like to see that back in the design.

You can find the colors and logo's on our website: www.hartuvo.nl

Industry/Entity Type

Business

Contact Information for Business Card

My Details:
Tobias Lindqvist

Phone: 0031687203316
E-mail: Tobias@hartuvo.nl

Slogan: "Because Quality Matters"

Font styles to use
Sans Serif

Colors

Designer to choose colors to be used in the design.

Requirements
Must have
• A Black backside with the Hartuvo logo on it. The front side should be clean with only my contact details.
• But I'm also open for something really different or awesome!
Nice to have
• Remember that we are in the parts & repairing industry, So i'll be handing those business cards mainly to repair companies. Maybe you can do something with that thought :)

```html
<!DOCTYPE html>
<html lang="en">
<head>
<meta charset="utf-8">
<title>Hartuvo business card</title>
<link rel="stylesheet" href="https://fonts.googleapis.com/css2?family=Open+Sans:wght@400;600;700&display=swap">
<style>
  :root {
    --orange: #f26f21;
    --black: #000000;
    --white: #ffffff;
    --ink: #555555;
    --rule: #cfcfcf;
    --backdrop: #e9e6e2;
  }
  * { margin: 0; padding: 0; box-sizing: border-box; }
  html, body { width: 1200px; height: 987px; overflow: hidden; background: var(--backdrop); }
  body { font-family: "Open Sans", Arial, sans-serif; position: relative; }
  .stack {
    position: absolute; left: 292px; top: 130px;
    width: 525px; height: 620px;
    transform: scale(1.1714); transform-origin: top left;
  }
  .card { position: absolute; left: 0; width: 525px; height: 300px; overflow: hidden; box-shadow: 0 2px 6px rgba(0,0,0,.25); }
  .card-front { top: 0; background: var(--white); }
  .card-back { top: 320px; background: var(--black); }

  .brand { position: absolute; left: 54px; top: 133px; display: flex; align-items: center; gap: 8px; }
  .brand-mark { width: 30px; height: 30px; background: var(--orange); }
  .brand-name { font-weight: 700; font-size: 34px; line-height: 1; color: var(--black); letter-spacing: -0.5px; }

  .divider { position: absolute; left: 295px; top: 97px; width: 1px; height: 105px; background: var(--rule); }

  .contact { position: absolute; left: 320px; top: 98px; }
  .contact-name { font-weight: 600; font-size: 18px; color: var(--orange); line-height: 24px; margin-bottom: 10px; }
  .contact-list { list-style: none; }
  .contact-list li { display: flex; align-items: center; gap: 6px; font-size: 13px; color: var(--ink); line-height: 20px; }
  .contact-list svg { width: 12px; height: 12px; flex: none; }

  .band { position: absolute; left: 0; bottom: 0; width: 525px; height: 20px; display: block; }

  .back-brand { position: absolute; left: 0; right: 0; top: 88px; text-align: center; font-weight: 700; font-size: 46px; color: var(--orange); line-height: 1; }
  .slogan { position: absolute; left: 0; right: 0; top: 238px; text-align: center; color: var(--white); font-weight: 600; font-size: 16px; }
</style>
</head>
<body>
  <div class="stack">
    <section class="card card-front">
      <div class="brand">
        <span class="brand-mark"></span>
        <span class="brand-name">hartuvo</span>
      </div>
      <div class="divider"></div>
      <div class="contact">
        <p class="contact-name">Tobias Lindqvist</p>
        <ul class="contact-list">
          <li>
            <svg viewBox="0 0 12 12" aria-hidden="true"><path fill="#f26f21" d="M2.3 0.6 L4 2.7 L3.1 4 Q4.2 6.6 7.9 8.9 L9.2 8 L11.4 9.7 L10.2 11.4 Q5.6 11.2 0.6 1.8 Z"/></svg>
            0031687203316
          </li>
          <li>
            <svg viewBox="0 0 12 12" aria-hidden="true"><rect x="0.5" y="2.5" width="11" height="7.5" fill="#f26f21"/><path d="M0.8 2.8 L6 6.8 L11.2 2.8" fill="none" stroke="#fff" stroke-width="1"/></svg>
            Tobias@hartuvo.nl
          </li>
          <li>
            <svg viewBox="0 0 12 12" aria-hidden="true"><circle cx="6" cy="6" r="5.5" fill="#f26f21"/><path d="M3 3.5 Q5 4 4.5 6 Q6.5 7 5.5 9.5 M8 2.5 Q7.5 4.5 9.5 5" fill="none" stroke="#fff" stroke-width="1"/></svg>
            www.hartuvo.nl
          </li>
        </ul>
      </div>
      <svg class="band" viewBox="0 0 525 20" preserveAspectRatio="none" aria-hidden="true">
        <polygon points="0,0 343,0 337,20 0,20" fill="#f26f21"/>
        <polygon points="349,0 525,0 525,20 343,20" fill="#000"/>
      </svg>
    </section>

    <section class="card card-back">
      <div class="back-brand">hartuvo</div>
      <p class="slogan">Because Quality Matters</p>
    </section>
  </div>
</body>
</html>
```